New Business Card for Web Design/Internet Marketing Company

Looking for a great looking new business card. We are a 10 year old web design, internet marketing and website management company that works mostly with small businesses.

Our new card needs to better match the colors and style of our website, be bold, extremely usable and slightly edgy.

Target Market(s)

Small/Medium businesses that have websites

Industry/Entity Type

Internet

Requirements
Must have
• Front and back design, full color, rounded corners please

Must use the colors/style of our website (JPG provided)

INFO FOR CARDS (as readable as possible please)
Mark Lenner
President/CEO
mark@trelvanmedia.example
Phone: 520-381-7459
Toll Free: 866-381-7459
Address: 4315 W. Calloway Ave. Ste. 140, Tucson, AZ 85792

THINGS I WANT TO PROMOTE (if there is room):
1. Our Website - www.trelvanmedia.example

2. Social Media
Twitter: @trelvanmedia
Facebook: www.facebook.com/trelvanmedia

3. Our Services
Web Design
Internet Marketing
Website Management

```html
<!DOCTYPE html>
<html lang="en">
<head>
<meta charset="utf-8">
<title>Trelvan Media – Business Card</title>
<link rel="stylesheet" href="https://fonts.googleapis.com/css2?family=Source+Sans+3:wght@400;600;700&display=swap">
<style>
  :root {
    --bg: #e8e5e1;
    --card-white: #ffffff;
    --slate: #5a5b5d;
    --orange: #f0812a;
    --blue: #1a8fc4;
    --text-grey: #555658;
    --rule-grey: #9a9b9d;
    --white: #ffffff;
  }
  * { box-sizing: border-box; margin: 0; padding: 0; }
  html, body {
    width: 1200px; height: 402px; overflow: hidden;
    background: var(--bg);
    font-family: "Source Sans 3", "Myriad Pro", Arial, sans-serif;
  }
  .card {
    position: absolute; top: 56px;
    width: 512px; height: 291px;
    border-radius: 4px; overflow: hidden;
    box-shadow: 0 1px 3px rgba(0,0,0,.18);
  }
  /* Front */
  .card--front { left: 62px; background: var(--card-white); }
  .front__band { position: absolute; left: 0; top: 0; width: 100%; height: 74px; background: var(--slate); }
  .front__stripe { position: absolute; left: 0; width: 100%; height: 2px; }
  .front__stripe--orange { top: 75px; background: var(--orange); }
  .front__stripe--blue { top: 79px; height: 2px; background: var(--blue); }
  .brand {
    position: absolute; left: 0; top: 98px; width: 100%;
    display: flex; justify-content: center; align-items: center; gap: 10px;
  }
  .brand__dot { width: 18px; height: 18px; border-radius: 50%; background: var(--orange); }
  .brand__name { font-size: 34px; font-weight: 700; color: var(--blue); line-height: 1; letter-spacing: -.3px; }
  .tagline {
    position: absolute; top: 140px; left: 0; width: 100%; padding-left: 90px;
    text-align: center; font-size: 12px; color: var(--text-grey);
  }
  .holder {
    position: absolute; top: 168px; left: 0; width: 100%; text-align: center;
    color: var(--blue); white-space: nowrap;
  }
  .holder__name { font-size: 17px; font-weight: 700; }
  .holder__title { font-size: 12.5px; font-weight: 400; }
  .contact { position: absolute; top: 212px; font-size: 12.5px; color: var(--text-grey); line-height: 18.5px; }
  .contact--left { right: 262px; text-align: right; }
  .contact--right { left: 272px; }
  .contact__row { display: flex; align-items: center; gap: 5px; white-space: nowrap; }
  .contact--left .contact__row { justify-content: flex-end; }
  .contact__address { margin-top: 4px; }
  .social-square { width: 10px; height: 10px; background: var(--rule-grey); border-radius: 1px; }
  .icon { width: 11px; height: 11px; fill: none; stroke: var(--text-grey); stroke-width: 1.3; flex: none; }
  .icon--solid { fill: var(--text-grey); stroke: none; }
  .contact__divider { position: absolute; left: 262px; top: 210px; width: 1px; height: 76px; background: var(--rule-grey); }
  /* Back */
  .card--back { left: 626px; background: var(--slate); color: var(--white); }
  .back__brand {
    position: absolute; left: 26px; top: 122px;
    font-size: 36px; font-weight: 700; color: var(--white); line-height: 1;
  }
  .services { position: absolute; left: 266px; top: 116px; }
  .services__title { font-size: 25px; font-weight: 600; margin-bottom: 14px; line-height: 1; }
  .services__list { list-style: none; font-size: 21px; line-height: 30px; font-weight: 400; }
</style>
</head>
<body>
  <section class="card card--front" aria-label="Card front">
    <div class="front__band"></div>
    <div class="front__stripe front__stripe--orange"></div>
    <div class="front__stripe front__stripe--blue"></div>

    <div class="brand">
      <span class="brand__dot"></span>
      <span class="brand__name">Trelvan Media</span>
    </div>
    <p class="tagline">Grow your Website</p>

    <p class="holder"><span class="holder__name">Mark Lenner,</span> <span class="holder__title">President/CEO</span></p>

    <div class="contact contact--left">
      <div class="contact__row"><span class="social-square"></span>trelvanmedia</div>
      <div class="contact__row"><span class="social-square"></span>@trelvanmedia</div>
      <div class="contact__address">4315 W. Calloway Ave. Ste. 140<br>Tucson, AZ 85792</div>
    </div>

    <div class="contact__divider"></div>

    <div class="contact contact--right">
      <div class="contact__row">
        <svg class="icon" viewBox="0 0 12 12"><circle cx="6" cy="6" r="5"/><path d="M4 3.5l1 1.5-.7.8a4 4 0 0 0 2 2l.8-.7 1.5 1"/></svg>520-381-7459
      </div>
      <div class="contact__row">
        <svg class="icon" viewBox="0 0 12 12"><circle cx="6" cy="6" r="5"/><path d="M4 8l4-4"/></svg>866-381-7459
      </div>
      <div class="contact__row">
        <svg class="icon icon--solid" viewBox="0 0 12 12"><path d="M1 3h10v6H1z"/><path d="M1 3l5 3.5L11 3" stroke="#fff" stroke-width="1" fill="none"/></svg>mark@trelvanmedia.example
      </div>
      <div class="contact__row">
        <svg class="icon" viewBox="0 0 12 12"><circle cx="6" cy="6" r="5"/><path d="M1 6h10M6 1c-2.5 3-2.5 7 0 10M6 1c2.5 3 2.5 7 0 10"/></svg>www.trelvanmedia.example
      </div>
    </div>
  </section>

  <section class="card card--back" aria-label="Card back">
    <div class="back__brand">Trelvan Media</div>
    <div class="services">
      <h2 class="services__title">Our Services</h2>
      <ul class="services__list">
        <li>Web Design</li>
        <li>Internet Marketing</li>
        <li>Website Management</li>
      </ul>
    </div>
  </section>
</body>
</html>
```